BrivoTerna. Lantern of the Steady Harvest. Business card

Professional business card for BrivoTerna (Lantern of the Steady Harvest)
My rationale: Strategy-> Execution-> Results-> Value that lead to the BrivoTerna name: We put the Lantern of the Steady Harvest.
We deliver value to our customers helping them at defining a good strategy (cyan arrow). 90% of well formulated strategies fail due to poor execution so we also consider strategical execution very important (green arrow). Due to the execution we obtain the results (blue arrow). Finally, the results provide feedback to redefine strategy, and the new strategy has to be executed and new results obtained providing new feedback and on and on. It's like a wheel that finally, must create corporate value: value for shareholders, staholders, employees, providers...-

Target Market(s)

CEOs and steering comitees , invewrnent funds

Industry/Entity Type

Business Consultant

Contact Information for Business Card

Teodoro Vinsquel
CEO & Founder
teodoro.vinsquel@brivoterna-example.com
Mobile: +34 655.803.912
www.brivoterna-example.com

Colors

Designer to choose colors to be used in the design.

Requirements
Nice to have
• Nice to hace the words: Strategy, execution, results
• Nice to vave the claim: Lantern of the Steady Harvest
• The three colors should be shown:
• cyan for STRATEGY
• green for EXECUTION
• blue for RESULTS
Should not have
• Complete black background

```html
<!DOCTYPE html>
<html lang="en">
<head>
<meta charset="utf-8">
<title>BrivoTerna – Business Card</title>
<link rel="stylesheet" href="https://fonts.googleapis.com/css2?family=Carlito:wght@400;700&display=swap">
<style>
  :root {
    --navy: #0a3192;
    --lime: #afce22;
    --green: #8cc63f;
    --cyan: #17aee8;
    --white: #ffffff;
    --card-grey: #eceded;
    --canvas: #e9eaea;
  }
  * { margin: 0; padding: 0; box-sizing: border-box; }
  html, body {
    width: 1200px;
    height: 851px;
    overflow: hidden;
  }
  body {
    background: var(--canvas);
    font-family: "Carlito", "Calibri", sans-serif;
    position: relative;
  }
  .card {
    position: absolute;
    top: 310px;
    width: 405px;
    height: 231px;
    overflow: hidden;
  }
  .card--front {
    left: 168px;
    background: radial-gradient(ellipse 55% 60% at 50% 48%, #ffffff 0%, #f5f6f6 45%, var(--card-grey) 100%);
  }
  .card--back {
    left: 628px;
    background: var(--lime);
  }
  .front-curve,
  .back-band {
    position: absolute;
    inset: 0;
    width: 100%;
    height: 100%;
  }
  .brand-name {
    position: absolute;
    left: 0;
    right: 0;
    top: 130px;
    text-align: center;
    font-weight: 700;
    font-size: 40px;
    letter-spacing: -1px;
    color: var(--navy);
    line-height: 1;
  }
  .pillars {
    position: absolute;
    left: 0;
    right: 0;
    top: 208px;
    text-align: center;
    font-size: 8.5px;
    letter-spacing: 1.8px;
    line-height: 1;
  }
  .pillars__strategy { color: var(--navy); }
  .pillars__execution { color: var(--green); }
  .pillars__results { color: var(--cyan); }
  .pillars__sep { color: #9aa0a6; margin: 0 6px; }

  .holder {
    position: absolute;
    right: 19px;
    top: 15px;
    text-align: right;
    color: var(--white);
    line-height: 1.05;
  }
  .holder__name { font-weight: 700; font-size: 14px; }
  .holder__role { font-size: 12px; opacity: 0.9; }
  .contact {
    position: absolute;
    right: 19px;
    top: 167px;
    text-align: right;
    color: var(--white);
    font-size: 13px;
    line-height: 18.5px;
    list-style: none;
  }
</style>
</head>
<body>
  <section class="card card--front" aria-label="Business card front">
    <svg class="front-curve" viewBox="0 0 405 231" preserveAspectRatio="none" aria-hidden="true">
      <path d="M292 231 C340 212 375 190 405 157 L405 231 Z" fill="var(--white)"/>
    </svg>
    <h1 class="brand-name">BrivoTerna</h1>
    <p class="pillars">
      <span class="pillars__strategy">STRATEGY</span><span class="pillars__sep">|</span><span class="pillars__execution">EXECUTION</span><span class="pillars__sep">|</span><span class="pillars__results">RESULTS</span>
    </p>
  </section>

  <section class="card card--back" aria-label="Business card back">
    <svg class="back-band" viewBox="0 0 405 231" preserveAspectRatio="none" aria-hidden="true">
      <polygon points="0,51 131,0 142,0 130,231 0,231" fill="var(--white)"/>
    </svg>
    <div class="holder">
      <p class="holder__name">Teodoro VINSQUEL</p>
      <p class="holder__role">CEO &amp; Founder</p>
    </div>
    <ul class="contact">
      <li>+34 655 803 912</li>
      <li>teodoro.vinsquel@brivoterna-example.com</li>
      <li>www.brivoterna-example.com</li>
    </ul>
  </section>
</body>
</html>
```